Card Design for my dog training business Brightpaw Obedience

Need a business card design for my dog training business with my new logo. Want the card to come off professional yet fun. Want it to be very eye catchy as well. I normally have these at vet clinics, pet stores, and groomers. so need it to look better than my competitors.
Target Market(s)
dog owners
Industry/Entity Type
Dog Training
Contact Information for Business Card
needs logo, my name and info
Font styles to use
Serif
Colors
0255a3
ffffff
ec1f27
000000
333333
fbfbfb
Requirements
Must have
- Brightpaw Obedience
- Felix Orland
- 415 903 2276
- info@brightpawobedience.example
- www.brightpawobedience.example

```html
<!DOCTYPE html>
<html lang="en">
<head>
<meta charset="utf-8">
<title>Brightpaw Obedience — Business Card</title>
<link rel="stylesheet" href="https://fonts.googleapis.com/css2?family=Tinos:ital,wght@0,400;0,700;1,400&family=EB+Garamond:ital@1&display=swap">
<style>
  :root {
    --ink: #000000;
    --paper: #ffffff;
    --stage: #2b2b2d;
    --soft: #fbfbfb;
    --muted: #d9d9d9;
    --serif: "Tinos", "Times New Roman", serif;
    --script: "EB Garamond", Georgia, serif;
  }
  * { box-sizing: border-box; margin: 0; padding: 0; }
  html, body { width: 1200px; height: 800px; overflow: hidden; }
  body {
    background: var(--stage);
    font-family: var(--serif);
    position: relative;
  }
  .card {
    position: absolute;
    top: 245px;
    width: 540px;
    height: 310px;
    border-radius: 20px;
    overflow: hidden;
    background: var(--ink);
  }
  .card--front { left: 30px; }
  .card--back { left: 630px; display: flex; }

  .brand {
    display: flex;
    flex-direction: column;
    align-items: center;
    justify-content: center;
    height: 100%;
    gap: 22px;
    text-align: center;
  }
  .brand__mark {
    display: flex;
    align-items: center;
    gap: 10px;
  }
  .brand__dot {
    width: 14px; height: 14px;
    border-radius: 50%;
    flex: none;
  }
  .brand__name {
    font-family: var(--serif);
    font-weight: 400;
    font-size: 26px;
    letter-spacing: 1px;
    white-space: nowrap;
  }
  .brand__tagline {
    font-family: var(--script);
    font-style: italic;
    font-size: 11px;
    white-space: nowrap;
  }

  .card--front .brand__name,
  .card--front .brand__tagline { color: var(--paper); }
  .card--front .brand__dot { background: var(--paper); }

  .back__logo-panel {
    width: 46%;
    background: var(--paper);
    color: var(--ink);
  }
  .back__logo-panel .brand__name { font-size: 19px; letter-spacing: 0.5px; color: var(--ink); }
  .back__logo-panel .brand__dot { background: var(--ink); width: 12px; height: 12px; }
  .back__logo-panel .brand__tagline { font-size: 9.5px; color: var(--ink); }

  .back__info {
    flex: 1;
    color: var(--paper);
    padding: 48px 22px 0 26px;
    position: relative;
  }
  .person__name {
    font-weight: 700;
    font-size: 19px;
    letter-spacing: 0.5px;
    text-transform: uppercase;
  }
  .person__role { font-size: 14px; margin-top: 2px; }
  .company { margin-top: 20px; font-size: 14px; line-height: 1.35; }
  .contact { list-style: none; margin-top: 14px; font-size: 13px; }
  .contact li { display: flex; align-items: center; gap: 9px; line-height: 1.55; white-space: nowrap; }
  .contact svg { width: 12px; height: 12px; flex: none; fill: var(--paper); }
  .social {
    position: absolute;
    right: 22px;
    bottom: 62px;
    display: flex;
    gap: 5px;
  }
  .social span {
    width: 20px; height: 20px;
    border-radius: 3px;
    background: var(--paper);
  }
</style>
</head>
<body>
  <section class="card card--front" aria-label="Business card front">
    <div class="brand">
      <div class="brand__mark">
        <span class="brand__dot"></span>
        <span class="brand__name">Brightpaw Obedience</span>
      </div>
      <p class="brand__tagline">“Good manners for happy dogs, one lesson at a time.”</p>
    </div>
  </section>

  <section class="card card--back" aria-label="Business card back">
    <div class="back__logo-panel">
      <div class="brand">
        <div class="brand__mark">
          <span class="brand__dot"></span>
          <span class="brand__name">Brightpaw Obedience</span>
        </div>
        <p class="brand__tagline">“Good manners for happy dogs, one lesson at a time.”</p>
      </div>
    </div>
    <div class="back__info">
      <h1 class="person__name">Felix Orland</h1>
      <p class="person__role">Trainer</p>
      <p class="company">Brightpaw Obedience<br>Cedar Ridge, Tx</p>
      <ul class="contact">
        <li>
          <svg viewBox="0 0 24 24" aria-hidden="true"><path d="M6.6 10.8c1.4 2.8 3.8 5.1 6.6 6.6l2.2-2.2c.3-.3.7-.4 1-.2 1.1.4 2.3.6 3.6.6.6 0 1 .4 1 1V20c0 .6-.4 1-1 1C10.6 21 3 13.4 3 4c0-.6.4-1 1-1h3.5c.6 0 1 .4 1 1 0 1.3.2 2.5.6 3.6.1.3 0 .7-.2 1z"/></svg>
          415 903 2276
        </li>
        <li>
          <svg viewBox="0 0 24 24" aria-hidden="true"><path d="M2 5h20v14H2z M2 5l10 8 10-8" stroke="#000" stroke-width="1.6"/></svg>
          info@brightpawobedience.example
        </li>
        <li>
          <svg viewBox="0 0 24 24" aria-hidden="true"><circle cx="12" cy="12" r="10"/><path d="M2 12h20M12 2c3 3 3 17 0 20M12 2c-3 3-3 17 0 20" stroke="#000" stroke-width="1.4" fill="none"/></svg>
          www.brightpawobedience.example
        </li>
      </ul>
      <div class="social" aria-hidden="true"><span></span><span></span></div>
    </div>
  </section>
</body>
</html>
```